Business Cards for IT Consulting Company (Managed Service Provider)

I am looking to have some business cards printed and would like some designs. We are an IT Consulting company based in Vancouver BC. I would like a nice clean and modern look to the cards. I have uploaded all the versions of my logo so parts can be used as needed. Here is a snippit from our website homepage:

Quillbrook Networks Ltd. is an IT Solutions Partner located in Vancouver BC, Canada. We offer IT solutions and support to customers in the greater Vancouver Area. With expertise in Microsoft platforms, as well as Linux and Mac OSX and over 12 years experience in the IT industry, Quillbrook Networks is dedicated to offering our clients top quality service and products. We take pride in the solutions we offer our customers. The greatest compliment a client can give us is to recommend our services.

Quillbrook Networks Ltd. offers a wide range of IT services from onsite service to remote support and managed service solutions. This allows clients to choose the support path that best suits their company’s needs. Supporting many different sized companies from small to enterprise level over the past 12 years Quillbrook Networks has the experience and expertise needed to ensure things run smoothly. Allowing our clients to focus on doing business.

Revolutionizing the way IT services are delivered.

Quillbrook Networks is dedicated to providing our clients with IT solutions that work and grow with them for years to come. This philosophy helps save money in the long run instead of replacing equipment constantly. Far too often IT solutions are not well thought out and while possibly solving the problem at hand, require replacement due to growth or quality within a very short time frame. Quillbrook Networks takes pride in providing solutions that will last and be able to accommodate growth without the need for replacement.

Industry/Entity Type

Information Technology

Contact Information for Business Card

Quillbrook Networks Ltd.
(Employee Name)
Eml: (Employees Email Address)
Web: quillbrook.me
Ph: 604-555-0148

Font styles to use
Serif
Sans Serif

Requirements
Must have
• The Company logo and company colors.
Nice to have
• - Our tag line: "Revolutionizing IT Services" or "Revolutionizing the way IT services are delivered."
• - Also I really like the idea of nature and technology together blending which is sort of where my logo came from so integrating that somehow onto the business cards would be great.

```html
<!DOCTYPE html>
<html lang="en">
<head>
<meta charset="utf-8">
<title>Quillbrook Networks Ltd. – Business Cards</title>
<link rel="stylesheet" href="https://fonts.googleapis.com/css2?family=Montserrat:wght@600&family=Roboto:ital,wght@0,400;0,500;1,400&display=swap">
<style>
  :root {
    --backdrop: #a9a8a8;
    --card-dark: #1f1f20;
    --card-light: #f2f2f2;
    --brand-blue: #1e8ad6;
    --text-light: #e6e6e6;
    --text-dark: #3a3a3a;
    --divider: #c9c9c9;
  }
  * { margin: 0; padding: 0; box-sizing: border-box; }
  html, body { width: 1200px; height: 1200px; overflow: hidden; }
  body {
    position: relative;
    background: var(--backdrop);
    font-family: "Roboto", Arial, sans-serif;
  }
  .card { position: absolute; width: 713px; }

  /* Front */
  .card-front {
    left: 238px; top: 117px; height: 420px;
    background: var(--card-dark);
  }
  .brand-lockup {
    position: absolute; left: 0; right: 0; top: 160px;
    display: flex; align-items: center; justify-content: center; gap: 16px;
  }
  .brand-mark {
    width: 22px; height: 22px; background: var(--brand-blue);
  }
  .brand-name {
    font-family: "Montserrat", Arial, sans-serif;
    font-weight: 600; font-size: 40px; color: var(--brand-blue);
    letter-spacing: 0.5px;
  }
  .tagline {
    position: absolute; left: 0; right: 0; top: 376px;
    display: flex; align-items: center; justify-content: center; gap: 15px;
  }
  .tagline-rule { width: 110px; height: 3px; background: var(--brand-blue); }
  .tagline-text { font-size: 19px; color: var(--text-light); letter-spacing: 0.3px; }

  /* Back */
  .card-back {
    left: 230px; top: 645px; height: 416px;
    background: var(--card-light);
  }
  .back-brand {
    position: absolute; left: 0; width: 341px; top: 188px;
    display: flex; align-items: center; justify-content: center; gap: 12px;
  }
  .back-brand .brand-mark { width: 18px; height: 18px; }
  .back-brand .brand-name { font-size: 24px; }
  .divider {
    position: absolute; left: 341px; top: 85px; width: 1px; height: 245px;
    background: var(--divider);
  }
  .contact { position: absolute; left: 400px; top: 128px; }
  .person-name { font-size: 25px; font-weight: 500; color: var(--brand-blue); }
  .person-title { margin-top: 4px; font-size: 16px; font-style: italic; color: var(--text-dark); }
  .contact-list { list-style: none; margin-top: 26px; }
  .contact-item {
    display: flex; align-items: center; gap: 18px;
    font-size: 18px; color: var(--text-dark); height: 27px;
  }
  .contact-icon { width: 18px; height: 16px; flex: none; }
</style>
</head>
<body>
  <section class="card card-front" aria-label="Business card front">
    <div class="brand-lockup">
      <span class="brand-mark"></span>
      <span class="brand-name">Quillbrook Networks Ltd.</span>
    </div>
    <div class="tagline">
      <span class="tagline-rule"></span>
      <span class="tagline-text">Revolutionizing IT Services</span>
      <span class="tagline-rule"></span>
    </div>
  </section>

  <section class="card card-back" aria-label="Business card back">
    <div class="back-brand">
      <span class="brand-mark"></span>
      <span class="brand-name">Quillbrook Networks</span>
    </div>
    <div class="divider"></div>
    <div class="contact">
      <p class="person-name">Daniel Harper</p>
      <p class="person-title">Managing Director</p>
      <ul class="contact-list">
        <li class="contact-item">
          <svg class="contact-icon" viewBox="0 0 18 16" aria-hidden="true">
            <rect x="2" y="2" width="14" height="3" rx="1.5" fill="#1e8ad6"/>
            <rect x="4" y="6" width="10" height="8" rx="1" fill="#1e8ad6"/>
            <circle cx="9" cy="10" r="2" fill="#f2f2f2"/>
          </svg>
          <span>604-555-0148</span>
        </li>
        <li class="contact-item">
          <svg class="contact-icon" viewBox="0 0 18 16" aria-hidden="true">
            <circle cx="9" cy="8" r="6.5" fill="none" stroke="#1e8ad6" stroke-width="1.6"/>
            <ellipse cx="9" cy="8" rx="2.8" ry="6.5" fill="none" stroke="#1e8ad6" stroke-width="1.3"/>
            <line x1="2.5" y1="8" x2="15.5" y2="8" stroke="#1e8ad6" stroke-width="1.3"/>
          </svg>
          <span>www.quillbrook.me</span>
        </li>
        <li class="contact-item">
          <svg class="contact-icon" viewBox="0 0 18 16" aria-hidden="true">
            <rect x="1.5" y="3" width="15" height="10" fill="#1e8ad6"/>
            <polyline points="1.5,3 9,9 16.5,3" fill="none" stroke="#f2f2f2" stroke-width="1.3"/>
          </svg>
          <span>support@quillbrook.me</span>
        </li>
      </ul>
    </div>
  </section>
</body>
</html>
```